Card Design Project

A simple, funky, cool birth announcement card
Not corporate, but arty
Not childish nor girlish
No baby pictures

Text is tbc (eg name and date may change)

Front side: just the name "fenna"
Should be easy to read

Back side text (in Dutch):

We vinden je nu al leuk!

20 JUNE 2013
Singapore

Dochter van Marieke Dorrel & Joost Vermalen

Yangon, Myanmar
+95 1 64 8319
Skype: Marieke.Dorrel
Skype: Joost.Vermalen

Size will be A6
Updates

Reason: Dear designers, At this stage we would like to have one or more designers to draft up the card (of which the final text is still tbd as the baby is yet to be born) using the typeface used on the left below (or similar!) of the newly added picture - in black - in fluorescent colours Can you get back to us in a few days? Thanks

Target Market(s)

Our funky friends in holland.

Industry/Entity Type

Baby

Requirements
Must have
• Colours, aswe are very happy to welcome this baby.
Something that makes it stand out from all other baby birth announcement cards

A6 size
Deadline 21 June
Printing will be on white (thick paper 250g)
Design for 5mm "bleedsides" all around
At least available in PDF (and other formats)
Nice to have
• We've recently moved from netherlands to Yangon
We could include the iconic kyauktaran pagoda

I would like for it to look like a cool party announcement

Include bright fluoriscent colours, including orange.
The enveloppe will be orange
Should not have
• Any baby stuff, soft pink dominance, childish stuff.

```html
<!DOCTYPE html>
<html lang="en">
<head>
<meta charset="utf-8">
<title>fenna — birth announcement front</title>
<link rel="stylesheet" href="https://fonts.googleapis.com/css2?family=Orbitron:wght@900&display=swap">
<style>
  :root {
    --paper: #ffffff;
    --frame: #0a1a9a;
    --deep-blue: #0b1f8c;
    --mid-blue: #1446d6;
    --bright-blue: #2a6cf0;
    --sky-blue: #3a8cf5;
    --glow-soft: rgba(180, 255, 230, 0.28);
    --glow-faint: rgba(120, 230, 210, 0.12);
    --glow-edge: #5ef0c0;
    --name: #ffffff;
  }
  html, body {
    margin: 0;
    padding: 0;
    width: 1200px;
    height: 1200px;
    overflow: hidden;
    background: var(--paper);
  }
  .canvas {
    position: relative;
    width: 1200px;
    height: 1200px;
    background: var(--paper);
  }
  .card-art {
    position: absolute;
    left: 44px;
    top: 44px;
    width: 1110px;
    height: 1110px;
    box-sizing: border-box;
    border: 3px solid var(--frame);
    border-radius: 4px;
    overflow: hidden;
    background:
      radial-gradient(circle at 40% 22%, var(--mid-blue) 0%, var(--deep-blue) 48%, transparent 49%),
      radial-gradient(circle at 10% 70%, var(--sky-blue) 0%, transparent 45%),
      linear-gradient(160deg, var(--bright-blue) 0%, var(--mid-blue) 45%, var(--deep-blue) 100%);
  }
  .backdrop-waves {
    position: absolute;
    inset: 0;
  }
  .light-scatter {
    position: absolute;
    left: 180px;
    top: 0;
    width: 930px;
    height: 900px;
    background:
      radial-gradient(ellipse 120px 420px at 66% 45%, var(--glow-soft) 0%, transparent 100%),
      radial-gradient(ellipse 380px 90px at 45% 42%, var(--glow-faint) 0%, transparent 100%);
  }
  .baby-name {
    position: absolute;
    left: 60px;
    top: 438px;
    margin: 0;
    font-family: "Orbitron", sans-serif;
    font-weight: 900;
    font-size: 160px;
    line-height: 1;
    letter-spacing: 14px;
    text-transform: uppercase;
    color: var(--name);
    text-shadow:
      0 0 12px var(--glow-edge),
      0 0 30px rgba(94, 240, 192, 0.6);
  }
</style>
</head>
<body>
<div class="canvas">
  <div class="card-art">
    <svg class="backdrop-waves" role="img" aria-label="Abstract blue background with halftone dot sphere and flowing wave lines" viewBox="0 0 1110 1110" preserveAspectRatio="none">
      <path d="M1010 0 C1070 330 900 650 420 720 C250 745 120 730 0 700" fill="none" stroke="#4f8dff" stroke-width="6" opacity="0.7"/>
      <path d="M1110 380 C900 620 700 760 380 800" fill="none" stroke="#6aa4ff" stroke-width="2" opacity="0.4"/>
      <path d="M1110 520 C880 700 720 860 560 1110" fill="none" stroke="#6aa4ff" stroke-width="2" opacity="0.35"/>
    </svg>
    <div class="light-scatter" role="img" aria-label="Scattered glowing mint light squares rising through the sky"></div>
    <h1 class="baby-name">fenna</h1>
  </div>
</div>
</body>
</html>
```